Website Design for Landscaping/Concrete Company

I need a website that is informative about what my company does and also offers before and after pictures of completed work. I already have a logo. The website must say "FREE ESTIMATES" somewhere and list a phone number. I would like to stick with the logo colors or similar (black and lime green).
Services Offered by Tomlet Builders:
Landscaping
Mowing
Concrete
Sidewalks
Brush Removal
Land Beautification

Please list the company name in large letters TOMLET BUILDERS
and also the contact information in large font.

Right now I am looking for a somewhat coverpage for my website. I don't have a lot of information for people to point and click on yet. Id like to get a coverpage to get my name out and then have a designer come back in a few months and update with more pictures and information.
Updates

If allowed please submit projects after due date. I made a mistake and only posted for one day. Thanks.

Coding

Coded - Design and coding required

```html
<!DOCTYPE html>
<html lang="en">
<head>
<meta charset="utf-8">
<title>Tomlet Builders</title>
<link href="https://fonts.googleapis.com/css2?family=Audiowide&family=Montserrat:wght@400;500;600;700&family=Roboto:wght@300;400&display=swap" rel="stylesheet">
<style>
:root{
  --green:#788c0b;
  --green-dark:#5f6f08;
  --lime:#8ab516;
  --ink:#111111;
  --grey-text:#8a8a8a;
  --panel:#f0f0f0;
  --line:#d4d4d4;
  --white:#ffffff;
  --black:#000000;
}
*{margin:0;padding:0;box-sizing:border-box}
html,body{width:1200px;height:4019px;overflow:hidden;background:var(--white)}
body{position:relative;font-family:'Montserrat',sans-serif;color:var(--ink)}
.abs{position:absolute}
.display{font-family:'Audiowide',sans-serif}

/* hero */
.hero{left:0;top:0;width:1200px;height:799px;background:linear-gradient(180deg,#2a3340 0%,#3b4a3c 45%,#3d5a22 75%,#2f4a1a 100%)}
.brand{display:flex;align-items:center;gap:10px;color:var(--white);font-family:'Montserrat',sans-serif;font-weight:700;font-size:17px;letter-spacing:1px;text-transform:uppercase;line-height:1.1;white-space:nowrap}
.brand .mark{width:18px;height:18px;background:var(--lime);flex:none}
.topline{top:34px;color:var(--white);font-size:16px;font-weight:500;display:flex;align-items:center;gap:10px;white-space:nowrap}
.nav{top:88px;left:568px;font-size:16px;font-weight:500;letter-spacing:1.5px;color:var(--white)}
.nav a{color:inherit;text-decoration:none;position:absolute;white-space:nowrap}
.nav .active{color:var(--lime)}
.hero-title{left:87px;top:336px;color:var(--white);font-size:60px;line-height:62px;letter-spacing:7px}
.hero-sub{left:87px;top:476px;color:var(--white);font-size:22px;line-height:30px;font-weight:500}
.btn{display:flex;align-items:center;justify-content:center;background:var(--green);color:var(--white);border-radius:30px;font-weight:600;font-size:18px}
.hero-btn{left:89px;top:568px;width:192px;height:56px}
.slide{top:337px;height:289px}
.slide span{position:absolute;left:20px;bottom:18px;color:var(--white);font-weight:700;font-size:32px;white-space:nowrap}
.arrow{left:1046px;top:451px;width:62px;height:62px;border:2px solid var(--white);border-radius:50%}

/* about */
.about-accent{left:362px;top:1163px;width:240px;height:234px;background:var(--green)}
.about-photo{left:89px;top:896px;width:467px;height:455px;background:linear-gradient(135deg,#5b8a2c,#8cc04a 55%,#c0477a 80%,#4f7a22)}
.about-label{left:556px;top:935px;width:424px;height:79px;background:var(--panel)}
.about-title{left:638px;top:947px;color:var(--green);font-size:48px;letter-spacing:2px}
.about-text{left:640px;top:1046px;width:474px;font-family:'Roboto',sans-serif;font-weight:300;font-size:16.5px;line-height:31.4px;color:var(--grey-text)}
.about-btn{left:640px;top:1294px;width:192px;height:54px}

/* services */
.section-title{left:0;width:1200px;text-align:center;font-size:46px;letter-spacing:2px}
.svc-img{width:318px}
.svc-label{width:319px;height:79px;background:var(--green);color:var(--white);display:flex;align-items:center;justify-content:center;font-weight:500;font-size:28px;letter-spacing:.5px;white-space:nowrap}

/* blog */
.blog{left:0;top:2366px;width:1200px;height:663px;background:linear-gradient(180deg,#6d8a10 0%,#5f7d1a 50%,#4d6e1c 100%)}
.blog-img{top:2523px;width:334px;height:219px}
.blog-card{top:2693px;width:307px;height:239px;background:var(--white);text-align:center}
.blog-card h3{margin:22px 18px 0;font-weight:500;font-size:23px;line-height:26px;color:var(--ink)}
.blog-card .date{margin-top:13px;font-family:'Roboto',sans-serif;font-size:14px;color:var(--green)}
.blog-card p{margin:12px 22px 0;font-family:'Roboto',sans-serif;font-weight:300;font-size:13.5px;line-height:25px;color:#555}
.blog-card .more{margin-top:8px;font-size:14px;font-weight:600;color:var(--green)}

/* contact */
.info-circle{width:52px;height:52px;border:1px solid var(--line);border-radius:50%;display:flex;align-items:center;justify-content:center}
.info-text{left:158px;font-size:16.5px;line-height:26px;color:#333;white-space:nowrap}
.social{top:3421px;width:52px;height:52px;border:1px solid var(--line);border-radius:50%}
.field{border:1px solid var(--line);font-family:'Roboto',sans-serif;font-size:15px;color:#777;padding:14px 16px}
.submit-btn{left:429px;top:3439px;width:190px;height:55px}

/* footer */
.footer{left:0;top:3591px;width:1200px;height:428px;background:var(--black)}
.footer-text{left:90px;top:3812px;width:410px;font-size:15px;line-height:25px;color:var(--white)}
.col-head{top:3680px;font-weight:600;font-size:17px;color:var(--white)}
.col-list{top:3734px;font-size:14.5px;line-height:31.5px;color:var(--white)}
.copyright{left:0;top:3971px;width:1200px;text-align:center;font-size:12px;font-weight:500;color:var(--white)}
</style>
</head>
<body>

<header class="abs hero" role="img" aria-label="Photo of a suburban house at dusk with a lawn and stone path"></header>
<div class="abs brand" style="left:90px;top:60px"><span class="mark"></span>Tomlet Builders</div>
<div class="abs topline" style="left:670px">
  <svg width="16" height="12" viewBox="0 0 16 12"><rect x="0.5" y="0.5" width="15" height="11" fill="#fff"/><path d="M1 1l7 6 7-6" fill="none" stroke="#3b4a3c" stroke-width="1.4"/></svg>
  hello@tomletbuilders.com
</div>
<div class="abs topline" style="left:953px">
  <svg width="14" height="14" viewBox="0 0 24 24"><path fill="#fff" d="M6.6 10.8a15 15 0 006.6 6.6l2.2-2.2c.3-.3.7-.4 1-.2 1.1.4 2.3.6 3.6.6.6 0 1 .4 1 1V20c0 .6-.4 1-1 1A17 17 0 013 4c0-.6.4-1 1-1h3.5c.6 0 1 .4 1 1 0 1.3.2 2.5.6 3.6.1.3 0 .7-.2 1z"/></svg>
  +1 555 014 2290
</div>
<nav class="abs nav">
  <a class="active" style="left:0">Home</a>
  <a style="left:100px">About Us</a>
  <a style="left:231px">Services</a>
  <a style="left:354px">Blog</a>
  <a style="left:442px">Contact Us</a>
</nav>
<h1 class="abs display hero-title">TOMLET<br>BUILDERS</h1>
<p class="abs hero-sub">Lorem ipsum dolor sit amet, consectetur adipiscing elit<br>Ut enim ad minim veniam, quis nostrud</p>
<div class="abs btn hero-btn">Free Estimates</div>
<div class="abs slide" style="left:719px;width:295px;background:linear-gradient(180deg,#3f7a1e,#6fb02e 60%,#5e9a22)" role="img" aria-label="Photo of a landscaped garden bed"><span>Landscaping</span></div>
<div class="abs slide" style="left:1033px;width:167px;overflow:hidden;background:linear-gradient(180deg,#b78a55,#6a8d3a 55%,#4e7a20)" role="img" aria-label="Photo of a freshly mown yard"><span>Mowing</span></div>
<div class="abs arrow"><svg width="58" height="58" viewBox="0 0 58 58"><path d="M26 21l8 8-8 8" fill="none" stroke="#fff" stroke-width="2.5"/></svg></div>

<section class="about">
  <div class="abs about-accent"></div>
  <div class="abs about-photo" role="img" aria-label="Photo of a curved lawn edged with flower beds"></div>
  <div class="abs about-label"></div>
  <h2 class="abs display about-title">ABOUT US</h2>
  <p class="abs about-text">Lorem ipsum dolor sit amet, consectetur adipiscing elit, sed do eiusmod tempor incididunt ut labore et dolore magna aliqua. Ut enim ad minim veniam, quis nostrud exercitation ullamco laboris nisi ut aliquip ex ea commodo consequat. Duis aute irure dolor in reprehenderit in voluptate velit esse cillum dolore eu fugiat nulla pariatur. Excepteur sint occaecat cupidatat non proident, sunt in culpa qui officia deserunt mollit anim id est laborum.</p>
  <div class="abs btn about-btn">Read More</div>
</section>

<section class="services">
  <h2 class="abs display section-title" style="top:1484px;color:var(--ink)">SERVICES OFFERED</h2>
  <div class="abs svc-img" style="left:90px;top:1560px;height:320px;background:linear-gradient(180deg,#6e9a3a,#9a9a8a 50%,#8fb23a)" role="img" aria-label="Photo of a paved garden path between hedges"></div>
  <div class="abs svc-img" style="left:435px;top:1560px;height:320px;background:linear-gradient(180deg,#c24a2a,#4c9a26 40%,#5aa82e)" role="img" aria-label="Photo of a lawn mower on grass"></div>
  <div class="abs svc-img" style="left:780px;top:1560px;height:320px;background:linear-gradient(180deg,#c9c9c4,#8aa0b8 50%,#d8d8d2)" role="img" aria-label="Photo of a worker cutting concrete"></div>
  <div class="abs svc-label" style="left:101px;top:1816px">Landscaping</div>
  <div class="abs svc-label" style="left:446px;top:1816px">Mowing</div>
  <div class="abs svc-label" style="left:791px;top:1816px">Concrete</div>

  <div class="abs svc-img" style="left:90px;top:1930px;height:322px;background:linear-gradient(135deg,#8aa84a,#c9c6bc 45%,#b8b5aa)" role="img" aria-label="Photo of a concrete sidewalk beside grass"></div>
  <div class="abs svc-img" style="left:435px;top:1930px;height:322px;background:linear-gradient(135deg,#b8cde0,#eef2f5 50%,#6d8eaa)" role="img" aria-label="Photo of a brush clearing snow"></div>
  <div class="abs svc-img" style="left:780px;top:1930px;height:322px;background:linear-gradient(180deg,#9fbfd8,#3f7a2a 35%,#4d8a2e)" role="img" aria-label="Photo of a tree-lined park"></div>
  <div class="abs svc-label" style="left:101px;top:2188px">Sidewalks</div>
  <div class="abs svc-label" style="left:446px;top:2188px">Brush Removal</div>
  <div class="abs svc-label" style="left:791px;top:2188px">Land Beautification</div>
</section>

<section class="abs blog" role="img" aria-label="Background photo of a green lawn"></section>
<h2 class="abs display section-title" style="top:2452px;color:var(--white)">LATEST BLOG</h2>
<div class="abs blog-img" style="left:89px;background:linear-gradient(180deg,#8aa86a,#5c7a2e)" role="img" aria-label="Photo of workers trimming tall grass"></div>
<div class="abs blog-img" style="left:434px;background:linear-gradient(180deg,#4a6a2e,#8c8a7a 60%,#6a8a3a)" role="img" aria-label="Photo of a patio with garden furniture"></div>
<div class="abs blog-img" style="left:777px;background:linear-gradient(135deg,#c8c6c0,#9a9890 50%,#3a7a4a)" role="img" aria-label="Photo of a worker laying paving stones"></div>
<article class="abs blog-card" style="left:103px"><h3>Lorem ipsum dolor sit amet, consectetur</h3><div class="date">20.12.2020</div><p>Lorem ipsum dolor sit amet, consectetur adipiscing elit, sed do eiusmod tempor</p><div class="more">Read More</div></article>
<article class="abs blog-card" style="left:446px"><h3>Lorem ipsum dolor sit amet, consectetur</h3><div class="date">20.12.2020</div><p>Lorem ipsum dolor sit amet, consectetur adipiscing elit, sed do eiusmod tempor</p><div class="more">Read More</div></article>
<article class="abs blog-card" style="left:791px"><h3>Lorem ipsum dolor sit amet, consectetur</h3><div class="date">20.12.2020</div><p>Lorem ipsum dolor sit amet, consectetur adipiscing elit, sed do eiusmod tempor</p><div class="more">Read More</div></article>

<section class="contact">
  <h2 class="abs display section-title" style="top:3118px;color:var(--ink)">CONTACT US</h2>
  <div class="abs info-circle" style="left:89px;top:3195px"><svg width="14" height="18" viewBox="0 0 14 18"><path d="M7 1a6 6 0 00-6 6c0 4.5 6 10 6 10s6-5.5 6-10a6 6 0 00-6-6z" fill="#8a8a8a"/><circle cx="7" cy="7" r="2.2" fill="#fff"/></svg></div>
  <div class="abs info-text" style="top:3191px">Lorem ipsum dolor sit amet,<br>consectetur adipiscing</div>
  <div class="abs info-circle" style="left:89px;top:3270px"><svg width="14" height="14" viewBox="0 0 24 24"><path fill="#8a8a8a" d="M6.6 10.8a15 15 0 006.6 6.6l2.2-2.2c.3-.3.7-.4 1-.2 1.1.4 2.3.6 3.6.6.6 0 1 .4 1 1V20c0 .6-.4 1-1 1A17 17 0 013 4c0-.6.4-1 1-1h3.5c.6 0 1 .4 1 1 0 1.3.2 2.5.6 3.6.1.3 0 .7-.2 1z"/></svg></div>
  <div class="abs info-text" style="top:3266px">Phone No<br>+1 555 014 2290</div>
  <div class="abs info-circle" style="left:89px;top:3346px"><svg width="16" height="12" viewBox="0 0 16 12"><rect width="16" height="12" fill="#8a8a8a"/><path d="M1 1l7 6 7-6" fill="none" stroke="#fff" stroke-width="1.4"/></svg></div>
  <div class="abs info-text" style="top:3342px">Email<br>hello@tomletbuilders.com</div>
  <div class="abs social" style="left:89px"></div>
  <div class="abs social" style="left:149px"></div>
  <div class="abs social" style="left:208px"></div>
  <div class="abs social" style="left:269px"></div>

  <div class="abs field" style="left:431px;top:3202px;width:335px;height:46px">First Name</div>
  <div class="abs field" style="left:776px;top:3202px;width:334px;height:46px">Last Name</div>
  <div class="abs field" style="left:431px;top:3257px;width:335px;height:46px">Email</div>
  <div class="abs field" style="left:776px;top:3257px;width:334px;height:46px">Phone No</div>
  <div class="abs field" style="left:431px;top:3311px;width:679px;height:118px">Message</div>
  <div class="abs btn submit-btn">Submit</div>
</section>

<footer class="abs footer"></footer>
<div class="abs brand" style="left:89px;top:3720px;font-size:20px"><span class="mark"></span>Tomlet Builders</div>
<p class="abs footer-text">Lorem ipsum dolor sit amet,<br>consectetur adipiscing elit, sed do eiusmod tempor incididunt ut labore et dolore magna aliqua</p>
<div class="abs col-head" style="left:799px">Links</div>
<div class="abs col-list" style="left:799px">Home<br>About Us<br>Services<br>Blog<br>Contact Us</div>
<div class="abs col-head" style="left:971px">Others</div>
<div class="abs col-list" style="left:971px">FAQ<br>Privacy Policy<br>Terms &amp; Conditions</div>
<div class="abs copyright">Copyrights © 2021, The Company Name. All rights reserved.</div>

</body>
</html>
```